Harbourline Electrical Solutions

On one side. LOGO (underneath:) Commercial Industrial Residential

- NAME & CONTACT DETAILS

Marcus T. Hollings
Project Manager

(Cell icon) (441) 555-0187
(Email icon) hlelectricalsolutions@mailvento.com
(Facebook & Instagram icons )@hlelectricalsolutions

Other side: LOGO - underneath ELECTRICAL CONSTRUCTION & MAINTENANCE . LED LIGHTING & AUTOMATION . LIFE SAFETY SYSTEMS (FIRE ALARM / SECURITY) . DATA & COMMUNICATION

```html
<!DOCTYPE html>
<html lang="en">
<head>
<meta charset="utf-8">
<title>Harbourline Electrical Solutions – Business Card</title>
<link rel="stylesheet" href="https://fonts.googleapis.com/css2?family=Montserrat:wght@400;500;600;700&display=swap">
<style>
  :root {
    --teal: #0f5468;
    --teal-dark: #0c4758;
    --ink: #4a4a4a;
    --paper: #ffffff;
    --backdrop: #e3e3e3;
    --rule: #8a8a8a;
  }
  * { margin: 0; padding: 0; box-sizing: border-box; }
  html, body { width: 1200px; height: 900px; overflow: hidden; }
  body {
    background: var(--backdrop);
    font-family: "Montserrat", Arial, sans-serif;
    position: relative;
  }
  .card {
    position: absolute;
    left: 320px;
    width: 560px;
    height: 320px;
    border-radius: 22px;
    overflow: hidden;
  }
  .card--back { top: 100px; background: var(--teal); color: var(--paper); }
  .card--front { top: 480px; background: var(--paper); color: var(--ink); }

  /* Back side */
  .back-name {
    position: absolute;
    top: 78px; left: 0; right: 0;
    text-align: center;
    font-weight: 600;
    font-size: 30px;
    letter-spacing: 1px;
    line-height: 1.2;
  }
  .services {
    position: absolute;
    top: 176px; left: 0; right: 0;
    list-style: none;
    text-align: center;
    font-size: 12.5px;
    font-weight: 500;
    letter-spacing: 1.3px;
    line-height: 1.55;
    text-transform: uppercase;
  }

  /* Front side */
  .brand {
    position: absolute;
    top: 46px; left: 40px;
  }
  .brand-name {
    color: var(--teal);
    font-weight: 600;
    font-size: 22px;
    letter-spacing: 0.6px;
    line-height: 1.2;
  }
  .sectors {
    margin-top: 8px;
    font-size: 12.5px;
    letter-spacing: 1.4px;
    text-transform: uppercase;
    color: var(--ink);
  }
  .social {
    position: absolute;
    top: 34px; right: 34px;
    display: flex; align-items: center; gap: 8px;
    font-size: 12.5px;
    color: var(--ink);
  }
  .social-dot {
    width: 16px; height: 16px;
    border: 1.5px solid var(--teal);
    border-radius: 50%;
  }
  .person {
    position: absolute;
    left: 40px; top: 176px;
  }
  .person-name {
    color: var(--teal);
    font-weight: 700;
    font-size: 19px;
    letter-spacing: 0.8px;
    text-transform: uppercase;
  }
  .person-role { font-size: 14px; margin-top: 2px; }
  .contacts {
    position: absolute;
    left: 40px; top: 248px;
    list-style: none;
    font-size: 14px;
    line-height: 1.7;
  }
  .contacts li { display: flex; align-items: center; gap: 8px; }
  .contacts svg { width: 14px; height: 14px; flex: none; }
</style>
</head>
<body>

<section class="card card--back">
  <div class="back-name">Harbourline<br>Electrical Solutions</div>
  <ul class="services">
    <li>Electrical Construction &amp; Maintenance</li>
    <li>LED Lighting &amp; Automation</li>
    <li>Data &amp; Communication</li>
    <li>Life Safety Systems (Fire Alarm / Security)</li>
  </ul>
</section>

<section class="card card--front">
  <div class="brand">
    <div class="brand-name">Harbourline Electrical Solutions</div>
    <div class="sectors">Commercial Industrial Residential</div>
  </div>

  <div class="social">
    <span class="social-dot" aria-hidden="true"></span>
    <span>@hlelectricalsolutions</span>
  </div>

  <div class="person">
    <div class="person-name">Marcus T. Hollings</div>
    <div class="person-role">Project Manager</div>
  </div>

  <ul class="contacts">
    <li>
      <svg viewBox="0 0 14 14" aria-hidden="true">
        <rect x="3" y="0.75" width="8" height="12.5" rx="1.5" fill="none" stroke="var(--teal)" stroke-width="1.5"/>
        <line x1="6" y1="11" x2="8" y2="11" stroke="var(--teal)" stroke-width="1.2"/>
      </svg>
      <span>(441) 555-0187</span>
    </li>
    <li>
      <svg viewBox="0 0 14 14" aria-hidden="true">
        <rect x="0.5" y="2.5" width="13" height="9" fill="var(--teal)"/>
        <polyline points="1,3 7,8 13,3" fill="none" stroke="#fff" stroke-width="1.2"/>
      </svg>
      <span>hlelectricalsolutions@mailvento.com</span>
    </li>
  </ul>
</section>

</body>
</html>
```